Business card design

I am open to ideas. I was thinking of a vertical design, turning the name 90 degrees and placing it on the left edge, then some clipped portion of the fabulous tree with contact info on the bottom -- special emphasis on Web address:WhimBeads.comFor All Your Beading Needs121 E. Cotati AveCotati, CA 94931(707) 664-8343

```html
<!DOCTYPE html>
<html lang="en">
<head>
<meta charset="utf-8">
<title>Fern Glass Co. – Business Card</title>
<link href="https://fonts.googleapis.com/css2?family=Arimo:wght@400;700&display=swap" rel="stylesheet">
<style>
  :root {
    --bg: #d6d6d6;
    --card-white: #ffffff;
    --ink: #111111;
    --ink-grey: #444444;
    --red: #e8171d;
    --orange: #f07a16;
    --yellow: #f2d21b;
    --green: #3fa535;
    --lime: #8cc63f;
    --blue: #1d4fa8;
    --purple: #6a2ca0;
    --white: #ffffff;
  }
  * { margin: 0; padding: 0; box-sizing: border-box; }
  html, body {
    width: 1200px; height: 900px; overflow: hidden;
    background: var(--bg);
    font-family: "Arimo", Arial, sans-serif;
  }
  .stage { position: relative; width: 1200px; height: 900px; }

  .card {
    position: absolute;
    width: 560px; height: 320px;
    border-radius: 26px;
    overflow: hidden;
    box-shadow: 0 8px 18px rgba(0,0,0,0.25);
  }

  /* Front */
  .card-front {
    left: 40px; top: 110px;
    background: linear-gradient(180deg, var(--red) 0%, var(--orange) 20%, var(--green) 42%, var(--blue) 66%, var(--purple) 100%);
  }
  .front-art-area {
    position: absolute; left: 200px; top: 40px;
    width: 160px; height: 130px;
    border-radius: 12px;
    background: radial-gradient(ellipse at 50% 50%, rgba(255,255,255,0.75), rgba(255,255,255,0.15) 80%);
  }
  .front-name {
    position: absolute; left: 0; right: 0; top: 186px;
    text-align: center;
    color: var(--white);
    font-size: 30px; font-weight: 400;
  }
  .front-tagline {
    position: absolute; left: 0; right: 0; top: 230px;
    text-align: center;
    color: var(--white);
    font-size: 13px; letter-spacing: 1px;
  }

  /* Back */
  .card-back {
    left: 600px; top: 470px;
    background: var(--card-white);
  }
  .back-art-area {
    position: absolute; left: 30px; top: 110px;
    width: 260px; height: 190px;
    border-radius: 12px;
    background: linear-gradient(90deg, var(--purple) 0%, var(--blue) 22%, var(--green) 45%, var(--yellow) 62%, var(--orange) 80%, var(--red) 100%);
    opacity: 0.55;
  }
  .back-name {
    position: absolute; right: 36px; top: 36px;
    color: var(--ink);
    font-size: 30px; font-weight: 400;
  }
  .back-contact {
    position: absolute; left: 316px; top: 108px;
    color: var(--ink);
  }
  .phone {
    font-size: 22px; font-weight: 700; color: var(--ink-grey);
    margin-bottom: 10px;
  }
  .address { font-size: 15px; line-height: 1.3; color: var(--ink); }
  .web {
    position: absolute; left: 316px; top: 226px;
    font-size: 19px; font-weight: 700;
    white-space: nowrap;
  }
  .web-prefix { color: var(--purple); }
  .web-name { color: var(--lime); }
  .web-suffix { color: var(--red); }
</style>
</head>
<body>
<div class="stage">

  <section class="card card-front">
    <div class="front-art-area" role="img" aria-label="White tree illustration with a rope swing over a faint leafy tree silhouette"></div>
    <div class="front-name">Fern Glass Co.</div>
    <div class="front-tagline">FOR ALL YOUR BEADING NEEDS</div>
  </section>

  <section class="card card-back">
    <div class="back-art-area" role="img" aria-label="Tree illustration with rainbow-coloured leaves and a rope swing"></div>
    <div class="back-name">Fern Glass Co.</div>
    <div class="back-contact">
      <p class="phone">(707) 555-0192</p>
      <p class="address">348 W. Brindle Ave<br>Alder Bay, CA 94960</p>
    </div>
    <p class="web"><span class="web-prefix">www.</span><span class="web-name">FernGlassco</span><span class="web-suffix">.com</span></p>
  </section>

</div>
</body>
</html>
```